Marlow Estate Fixers (Handyman / Home Improvement Company)

Looking for a double sided professional looking business card with Logo attached to be highlighted on one side and throwing in an image of a handyman as an option would be nice to see as well. We are a company focused on providing quality Handyman and Home improvement services in a timely manner that is done right the first time with integrity

Industry/Entity Type

Handyman / Home Improvement

Contact Information for Business Card

(LOGO, Name, Mobile and office phone numbers, email) on front side of card, (the words "The SOLUTION to all of your Handyman and Home Improvement needs" followed by "Family Owned and Operated" at the very bottom) on the back.

Colors
EB3D1F
EC4F4E
F09395
F8D3D4
FCEDEE

Requirements
Must have
• Red, Gray, Black Color scheme
Should not have
• No Yellow or Blue colors

```html
<!DOCTYPE html>
<html lang="en">
<head>
<meta charset="utf-8">
<title>Marlow Estate Fixers – Business Cards</title>
<link href="https://fonts.googleapis.com/css2?family=Montserrat:wght@400;500;600;800&display=swap" rel="stylesheet">
<style>
  :root {
    --bg: #1a1a1b;
    --card: #1e1e1f;
    --red: #eb3d1f;
    --white: #ffffff;
    --grey: #d4d4d4;
    --line: #b8322a;
  }
  * { margin: 0; padding: 0; box-sizing: border-box; }
  html, body { width: 1200px; height: 875px; overflow: hidden; }
  body {
    background: var(--bg);
    font-family: "Montserrat", sans-serif;
    position: relative;
  }
  .card {
    position: absolute;
    width: 540px;
    height: 310px;
    background: var(--card);
    border-radius: 16px;
    box-shadow: 0 18px 40px rgba(0,0,0,0.55);
  }
  .card-back { left: 50px; top: 150px; }
  .card-front { left: 610px; top: 415px; }

  .brand {
    display: flex;
    align-items: center;
    gap: 12px;
    color: var(--red);
    font-weight: 800;
    text-transform: uppercase;
    line-height: 1.05;
  }
  .brand-dot {
    flex: none;
    border-radius: 50%;
    background: var(--red);
  }

  /* Back side: brand, tagline, family line */
  .card-back {
    display: flex;
    flex-direction: column;
    align-items: center;
    padding: 46px 40px 26px;
    text-align: center;
  }
  .card-back .brand { font-size: 30px; }
  .card-back .brand-dot { width: 36px; height: 36px; }
  .tagline {
    margin-top: 26px;
    color: var(--white);
    font-size: 15px;
    font-weight: 500;
    line-height: 1.45;
    max-width: 400px;
  }
  .tagline strong { color: var(--red); font-weight: 800; }
  .family-line {
    margin-top: auto;
    color: var(--grey);
    font-size: 12px;
    font-weight: 600;
    letter-spacing: 2px;
    text-transform: uppercase;
  }

  /* Front side: brand + contact */
  .card-front .brand {
    position: absolute;
    left: 34px; top: 50%;
    transform: translateY(-50%);
    font-size: 21px;
    width: 220px;
  }
  .card-front .brand-dot { width: 26px; height: 26px; }

  .divider {
    position: absolute;
    left: 272px; top: 60px;
    width: 1px; height: 190px;
    background: var(--line);
  }
  .contact {
    position: absolute;
    left: 292px; top: 62px;
    color: var(--grey);
    font-size: 12.5px;
  }
  .contact-name {
    font-size: 24px;
    font-weight: 800;
    color: var(--white);
    line-height: 1.1;
  }
  .contact-name .surname { color: var(--red); }
  .contact-role { margin: 2px 0 10px; font-weight: 500; }
  .contact-address { line-height: 1.35; margin-bottom: 10px; }
  .contact-list { list-style: none; }
  .contact-list li {
    display: flex; align-items: center; gap: 8px;
    line-height: 1.7;
  }
  .contact-list svg { width: 12px; height: 12px; fill: var(--red); flex: none; }
</style>
</head>
<body>

  <section class="card card-back" aria-label="Card back">
    <div class="brand"><span class="brand-dot"></span><span>Marlow Estate<br>Fixers</span></div>
    <p class="tagline">The <strong>SOLUTION</strong> to all of your Handyman and Home Improvement needs</p>
    <p class="family-line">Family Owned and Operated</p>
  </section>

  <section class="card card-front" aria-label="Card front">
    <div class="brand"><span class="brand-dot"></span><span>Marlow Estate<br>Fixers</span></div>
    <div class="divider"></div>
    <div class="contact">
      <p class="contact-name">Daniel <span class="surname">Reyes</span></p>
      <p class="contact-role">Managing Director</p>
      <p class="contact-address">48 Harbor Lane,<br>Marlow, USA</p>
      <ul class="contact-list">
        <li>
          <svg viewBox="0 0 24 24"><path d="M6.6 10.8a15.1 15.1 0 0 0 6.6 6.6l2.2-2.2c.3-.3.7-.4 1-.2 1.1.4 2.3.6 3.6.6.6 0 1 .4 1 1V20c0 .6-.4 1-1 1A17 17 0 0 1 3 4c0-.6.4-1 1-1h3.5c.6 0 1 .4 1 1 0 1.3.2 2.5.6 3.6.1.3 0 .7-.2 1z"/></svg>
          (08) 4410 2286
        </li>
        <li>
          <svg viewBox="0 0 24 24"><path d="M2 5h20v14H2zm2 2v.5l8 5 8-5V7l-8 5z"/></svg>
          hello@marlowfixers.com
        </li>
        <li>
          <svg viewBox="0 0 24 24"><path d="M12 2a10 10 0 1 0 0 20 10 10 0 0 0 0-20zm6.9 9h-3a15 15 0 0 0-1.3-5.6A8 8 0 0 1 18.9 11zM12 4.1c.9 1.3 1.7 3.9 1.9 6.9h-3.8c.2-3 1-5.6 1.9-6.9zM9.4 5.4A15 15 0 0 0 8.1 11h-3a8 8 0 0 1 4.3-5.6zM5.1 13h3a15 15 0 0 0 1.3 5.6A8 8 0 0 1 5.1 13zm6.9 6.9c-.9-1.3-1.7-3.900-1.9-6.9h3.8c-.2 3-1 5.6-1.9 6.9zm2.6-1.3a15 15 0 0 0 1.3-5.6h3a8 8 0 0 1-4.3 5.6z"/></svg>
          www.marlowfixers.com
        </li>
      </ul>
    </div>
  </section>

</body>
</html>
```